Mortgage Specialist Wordpress Build

I have a current WordPress site but I would like a whole new site built using the same domain. I've included a site for reference in my outline. The main focus of the website is to educate and capture leads.
I would like my blogs to stay for SEO already earned. Please see work requested attached.
Updates
Project Deadline Extended Reason: I am extending the deadline because I didn't realize this was a design only and I need the website coded as well. I've purchased the add-on. This is my first time using Pixel Harbor so please bare with me. I have additional Wordpress sites I want to have built too. Thanks, Colin Added Tuesday, April 18, 2017
Target Market(s)
Home Buyers, Home owners looking to refinance or renew their mortgages
Industry/Entity Type
Mortgage
Coding
Coded - Design and coding required
Font styles to use
Look and feel
Each slider illustrates characteristics of the customer's brand and the style your logo design should communicate.

```html
<!DOCTYPE html>
<html lang="en">
<head>
<meta charset="utf-8">
<title>Keystone Lending Group – North Vancouver Mortgage Broker</title>
<link rel="stylesheet" href="https://fonts.googleapis.com/css2?family=Open+Sans:wght@400;600;700&family=Dancing+Script:wght@500&display=swap">
<style>
:root{
  --yellow:#f2c31b;
  --navy:#0e3a78;
  --ink:#222;
  --muted:#666;
  --line:#d9d9d9;
  --band:#f6f6f7;
  --white:#fff;
}
*{box-sizing:border-box;margin:0;padding:0}
html,body{width:1200px;height:2532px;overflow:hidden;background:var(--white)}
body{position:relative;font-family:"Open Sans",Arial,sans-serif;color:var(--ink)}
.abs{position:absolute}

/* header */
.site-header{position:absolute;left:0;top:0;width:1200px;height:102px;background:var(--white)}
.brand{position:absolute;left:100px;top:28px;display:flex;align-items:center;gap:10px}
.brand-mark{width:26px;height:26px;background:var(--ink)}
.brand-name{font-size:19px;font-weight:700;color:var(--ink);letter-spacing:.3px}
.nav a{position:absolute;top:40px;font-size:14px;color:var(--ink);text-decoration:none}
.nav .active{color:var(--yellow)}
.btn-signin{position:absolute;left:1007px;top:31px;width:93px;height:42px;background:var(--yellow);color:var(--white);font-size:14px;font-weight:600;display:flex;align-items:center;justify-content:center}

/* hero */
.hero{position:absolute;left:0;top:102px;width:1200px;height:448px;background:linear-gradient(90deg,#c7d2d6 0%,#a9bcc6 40%,#b9c1c4 70%,#dcdcdc 100%)}
.hero-title{position:absolute;left:0;top:185px;width:1200px;text-align:center;font-size:51px;font-weight:700;color:var(--white);letter-spacing:-.5px}
.hero-btn{position:absolute;top:273px;height:54px;font-size:16px;font-weight:600;color:var(--white);display:flex;align-items:center;justify-content:center}
.hero-btn.primary{left:430px;width:170px;background:var(--yellow)}
.hero-btn.ghost{left:617px;width:152px;border:2px solid var(--white)}
.play{position:absolute;left:576px;top:358px}

/* lenders */
.lenders{position:absolute;left:0;top:550px;width:1200px;height:152px;background:var(--band)}
.lender{position:absolute;top:50px;height:50px;background:#dfe2e6;border-radius:4px}

/* services */
.section-title{position:absolute;left:0;width:1200px;text-align:center;font-size:34px;color:var(--ink)}
.card{position:absolute;top:848px;width:317px;height:332px;border:2px solid #e1e1e1;background:var(--white);text-align:center}
.card svg{position:absolute;left:118px;top:44px}
.card h3{position:absolute;left:0;top:138px;width:100%;font-size:20px;font-weight:400}
.card p{position:absolute;left:20px;top:182px;width:277px;font-size:12.5px;line-height:22px;color:var(--muted)}
.card .apply{position:absolute;left:106px;top:242px;width:104px;height:40px;border:1.5px solid var(--navy);color:var(--navy);font-size:12px;display:flex;align-items:center;justify-content:center}

/* questions band */
.ask-band{position:absolute;left:0;top:1253px;width:1200px;height:275px;background:linear-gradient(180deg,#2a2c30,#3d4046 60%,#2c2e33)}
.ask-title{position:absolute;left:0;top:50px;width:1200px;text-align:center;font-size:38px;font-weight:700;color:var(--white)}
.ask-field{position:absolute;left:214px;top:155px;width:683px;height:55px;background:var(--white);font-size:11px;color:#999;padding:20px 34px}
.ask-btn{position:absolute;left:897px;top:155px;width:89px;height:55px;background:var(--yellow);color:var(--white);font-weight:700;font-size:17px;display:flex;align-items:center;justify-content:center}

/* broker */
.broker{position:absolute;left:0;top:1528px;width:1200px;height:607px;background:#f7f8fa}
.broker-photo{position:absolute;left:97px;top:87px;width:333px;height:437px;background:linear-gradient(180deg,#5a5d62,#2c2e33)}
.broker h2{position:absolute;left:473px;top:98px;font-size:24px;font-weight:400}
.broker-copy{position:absolute;left:475px;top:150px;width:630px;font-size:12.5px;line-height:29px;color:var(--muted)}
.broker-copy p+p{margin-top:6px}
.reach{position:absolute;left:475px;top:390px;font-family:"Dancing Script",cursive;font-size:26px;color:var(--yellow)}
.app-btn{position:absolute;left:475px;top:452px;width:238px;height:55px;border:1.5px solid var(--navy);background:var(--white);color:var(--navy);font-size:13px;font-weight:700;display:flex;align-items:center;justify-content:center;gap:8px}
.social-sq{position:absolute;top:461px;width:36px;height:36px;border-radius:5px}

/* footer */
.footer{position:absolute;left:0;top:2135px;width:1200px;height:397px;background:var(--white);border-top:2px solid var(--navy)}
.f-head{position:absolute;top:66px;font-size:15px;font-weight:600;color:var(--ink)}
.f-row{position:absolute;display:flex;align-items:flex-start;gap:16px;font-size:12.5px;line-height:22px;color:#444}
.f-row svg{flex:none;margin-top:3px}
.circle-ico{width:26px;height:26px;border:1.5px solid #555;border-radius:50%;flex:none;margin-top:-2px}
.news-copy{position:absolute;left:572px;top:99px;width:270px;font-size:12px;line-height:22px;color:#444}
.mail-field{position:absolute;left:572px;top:159px;width:260px;height:42px;border:1.5px solid var(--line);font-size:11px;color:#666;padding:13px 12px}
.subscribe{position:absolute;left:572px;top:218px;width:98px;height:40px;background:var(--navy);color:var(--white);font-size:12px;font-weight:700;display:flex;align-items:center;justify-content:center}
.f-brand{position:absolute;left:892px;top:92px;width:210px;text-align:center;font-size:17px;font-weight:700;color:var(--ink)}
.f-badge{position:absolute;left:959px;top:200px;width:76px;height:76px;border-radius:50%;background:var(--navy)}
.f-rule{position:absolute;left:97px;top:313px;width:1006px;height:1px;background:#e3e3e3}
.copyright{position:absolute;left:0;top:346px;width:1200px;text-align:center;font-size:12px;color:#333}
</style>
</head>
<body>

<header class="site-header">
  <div class="brand"><span class="brand-mark"></span><span class="brand-name">Keystone Lending Group</span></div>
  <nav class="nav">
    <a class="active" style="left:534px">Home</a>
    <a style="left:660px">About</a>
    <a style="left:785px">Blog</a>
    <a style="left:900px">Contact</a>
  </nav>
  <div class="btn-signin">SIGN IN</div>
</header>

<section class="hero" role="img" aria-label="Smiling couple holding keys and a small model house">
  <h1 class="hero-title">BUYING YOUR DREAM HOME</h1>
  <div class="hero-btn primary">Get Hooked Up</div>
  <div class="hero-btn ghost">I'm a client</div>
  <svg class="play" width="48" height="48" viewBox="0 0 48 48"><circle cx="24" cy="24" r="21" fill="none" stroke="#fff" stroke-width="3"/><path d="M19 14l14 10-14 10z" fill="#fff"/></svg>
</section>

<section class="lenders" aria-label="Lender partners">
  <div class="lender" style="left:130px;width:112px"></div>
  <div class="lender" style="left:300px;width:112px"></div>
  <div class="lender" style="left:482px;width:96px"></div>
  <div class="lender" style="left:650px;width:86px"></div>
  <div class="lender" style="left:820px;width:66px"></div>
  <div class="lender" style="left:960px;width:106px"></div>
</section>

<h2 class="section-title" style="top:762px">I need help with</h2>

<article class="card" style="left:100px">
  <svg width="80" height="72" viewBox="0 0 80 72"><path d="M40 4L4 36h10v32h20V48h12v20h20V36h10z" fill="var(--navy)"/><rect x="54" y="8" width="8" height="16" fill="var(--navy)"/></svg>
  <h3>Purchase</h3>
  <p>Purchasing a home can be a daunting task as the market continues to sizzle essential...</p>
  <div class="apply">APPLY NOW</div>
</article>
<article class="card" style="left:441px">
  <svg width="84" height="84" viewBox="0 0 84 84" fill="none" stroke="var(--navy)" stroke-width="4"><path d="M12 42A30 30 0 0 1 66 22"/><path d="M72 42A30 30 0 0 1 18 62"/><path d="M58 20l9 2 1-9" /><path d="M26 64l-9-2-1 9"/><text x="42" y="53" text-anchor="middle" font-family="Open Sans,sans-serif" font-size="30" font-weight="700" fill="var(--navy)" stroke="none">$</text></svg>
  <h3 style="top:142px">Refinance</h3>
  <p style="top:186px">Want to pull out some equity or need to sell your property? you need to consolidate...</p>
  <div class="apply" style="top:246px">APPLY NOW</div>
</article>
<article class="card" style="left:784px">
  <svg width="80" height="80" viewBox="0 0 80 80" fill="none" stroke="var(--navy)" stroke-width="3"><path d="M10 40A30 30 0 0 1 62 20"/><path d="M70 40A30 30 0 0 1 18 60"/><path d="M54 18l9 2 1-9"/><path d="M26 62l-9-2-1 9"/></svg>
  <h3 style="top:130px">Renewal</h3>
  <p style="top:172px">It's best to start looking for new financing 120 days It's neve before your maturity....</p>
  <div class="apply" style="top:236px">APPLY NOW</div>
</article>

<section class="ask-band" role="img" aria-label="Dim desk scene with house plans and a laptop">
  <h2 class="ask-title">Mortgage or Real Estate Questions?</h2>
  <div class="ask-field">Search Our Knowlede base....</div>
  <div class="ask-btn">ASK</div>
</section>

<section class="broker">
  <div class="broker-photo" role="img" aria-label="Portrait of the mortgage broker in a dark suit"></div>
  <h2>North Vancouver Mortgage Broker</h2>
  <div class="broker-copy">
    <p>Purchasing a home, refinancing a mortgage and renewing a mortgage have one thing in common: they can represent an exciting time in an individual's life but they can also be complex.I am dedicated to giving back to the region by helping people save thousands of dollars in interest and prepayment expenses and find solutions that are fitted to your specific situation.</p>
    <p>In addition to getting you a fantastic rate, I ensure that I take enough time for each and every one of my clients to go over every detail in order to see that their mortgage repayment schedule is on track with their financial objectives. It is my mission to help people in this wonderful area get the best North Vancouver mortgage package possible while providing tremendous care and service.</p>
  </div>
  <div class="reach">You can reach me at 604.555.0148</div>
  <div class="app-btn"><svg width="12" height="12" viewBox="0 0 12 12"><path d="M5 0h2v6h3L6 10 2 6h3zM0 11h12v1H0z" fill="var(--navy)"/></svg>Download My Mortgage App</div>
  <span class="social-sq" style="left:745px;background:#3b5998"></span>
  <span class="social-sq" style="left:786px;background:#2aa3ef"></span>
  <span class="social-sq" style="left:827px;background:#0e76a8"></span>
  <span class="social-sq" style="left:868px;background:#cb2027"></span>
  <span class="social-sq" style="left:909px;background:#dd4b39"></span>
</section>

<footer class="footer">
  <div class="f-head" style="left:95px">CONTACT US</div>
  <div class="f-row" style="left:95px;top:104px"><svg width="14" height="18" viewBox="0 0 14 18"><path d="M7 1a6 6 0 0 1 6 6c0 4-6 10-6 10S1 11 1 7a6 6 0 0 1 6-6z" fill="none" stroke="#444" stroke-width="1.4"/><circle cx="7" cy="7" r="2" fill="none" stroke="#444" stroke-width="1.4"/></svg><span style="margin-left:6px">118 Harbourview Ave.<br>North Vancouver, BC V7M 0A1</span></div>
  <div class="f-row" style="left:95px;top:166px"><svg width="16" height="16" viewBox="0 0 16 16"><path d="M3 1l3 3-2 2c1 2 3 4 6 6l2-2 3 3-2 2C7 15 1 9 1 3z" fill="none" stroke="#444" stroke-width="1.3"/></svg><span style="margin-left:6px">Phone : &nbsp;(604).555.0148</span></div>
  <div class="f-row" style="left:95px;top:210px"><svg width="18" height="16" viewBox="0 0 18 16"><rect x="1" y="5" width="16" height="10" fill="none" stroke="#444" stroke-width="1.4"/><rect x="4" y="1" width="10" height="4" fill="none" stroke="#444" stroke-width="1.4"/><path d="M5 9h8M5 12h8" stroke="#444"/></svg><span style="margin-left:4px">Fax: 604.555.0192</span></div>
  <div class="f-row" style="left:95px;top:256px"><svg width="20" height="14" viewBox="0 0 20 14"><rect x="1" y="1" width="18" height="12" fill="none" stroke="#444" stroke-width="1.4"/><path d="M1 1l9 7 9-7" fill="none" stroke="#444" stroke-width="1.4"/></svg><span style="margin-left:2px">colin@harbourmortgage.ca</span></div>

  <div class="f-head" style="left:387px;top:61px">SOCIAL MEDIA</div>
  <div class="f-row" style="left:387px;top:115px"><span class="circle-ico"></span>Circlebook</div>
  <div class="f-row" style="left:387px;top:159px"><span class="circle-ico"></span>Chirper</div>
  <div class="f-row" style="left:387px;top:203px"><span class="circle-ico"></span>Orbit+</div>
  <div class="f-row" style="left:387px;top:247px"><span class="circle-ico"></span>Linkline</div>

  <div class="f-head" style="left:572px;top:62px">SIGNUP OUR NEWSLETTER</div>
  <p class="news-copy">Add your email below to receive my monthly mortgage update &amp; to join our VIP Club.</p>
  <div class="mail-field">Enter Mail</div>
  <div class="subscribe">SUBSCRIBE</div>

  <div class="f-brand">Keystone Lending Group</div>
  <div class="f-badge" aria-label="Anniversary badge"></div>

  <div class="f-rule"></div>
  <div class="copyright">© Copyright &nbsp;Keystone Lending Group .2017. All rights reserved.</div>
</footer>

</body>
</html>
```